New Business Card Design Project

We require a business card design for Vexalund, a newly established Indian company.
Our focus is on the development, manufacturing, and export of a diverse array of pharmaceutical products on a global scale. The card should convey a professional appearance, as our primary markets are in Africa, China, and Southeast Asian nations.
We envision a two-sided business card, with the reverse side dedicated to a logo set against a solid color or an elegantly designed pattern. The corners should be rounded. We would appreciate seeing both horizontal and vertical design options. We trust the designer to utilize their expertise in creating this design.

The content for the business card is included in the attached Word file.

Target Market(s)

Our primary markets are in Africa, China, and Southeast Asian, Latin America, Maldives, Sri Lanka

Industry/Entity Type

Pharmaceutical Manufacturing and Export

Contact Information for Business Card

Colors

Designer to choose colors to be used in the design.

Requirements
Must have
• The reverse side of the business card features solely the logo along with the tagline, "Care Beyond Borders."
Should not have
• The logo should not exceed two instances, encompassing both the front and back sides of the card.

```html
<!DOCTYPE html>
<html lang="en">
<head>
<meta charset="utf-8">
<title>Vexalund Business Card</title>
<link rel="stylesheet" href="https://fonts.googleapis.com/css2?family=Lexend:wght@300;400;500;600&display=swap">
<style>
  :root {
    --bg: #2a2a2a;
    --brand-blue: #2a9fd6;
    --brand-red: #e25443;
    --paper: #efefef;
    --ink: #2b2b2b;
    --white: #f4f4f4;
  }
  * { margin: 0; padding: 0; box-sizing: border-box; }
  html, body { width: 1200px; height: 1138px; overflow: hidden; background: var(--bg); }
  body { position: relative; font-family: "Lexend", sans-serif; }

  .card { position: absolute; border-radius: 18px; overflow: hidden; }

  .card-reverse {
    left: 274px; top: 185px; width: 624px; height: 378px;
    background: var(--brand-blue);
  }
  .card-reverse .brand-name {
    position: absolute; left: 0; width: 100%; top: 228px;
    text-align: center; color: var(--white);
    font-weight: 600; font-size: 56px; line-height: 56px; letter-spacing: -0.5px;
  }
  .card-reverse .tagline {
    position: absolute; left: 0; width: 100%; top: 283px;
    text-align: center; color: var(--white);
    font-weight: 300; font-size: 13px; line-height: 16px; letter-spacing: 8px; text-transform: uppercase;
    padding-left: 8px;
  }

  .card-front {
    left: 275px; top: 607px; width: 620px; height: 376px;
    background: var(--paper);
  }
  .card-front .wave { position: absolute; left: 0; top: 0; width: 620px; height: 376px; }
  .person { position: absolute; right: 37px; top: 30px; text-align: right; color: var(--white); }
  .person-name { font-weight: 500; font-size: 24px; line-height: 28px; }
  .person-role { font-weight: 300; font-size: 14px; line-height: 20px; margin-top: 2px; }

  .card-front .brand-name {
    position: absolute; left: 44px; top: 200px;
    color: var(--brand-blue); font-weight: 600; font-size: 56px; line-height: 60px; letter-spacing: -0.5px;
  }

  .address {
    position: absolute; left: 38px; top: 300px; font-style: normal;
    color: var(--ink); font-weight: 300; font-size: 15px; line-height: 22px;
  }
  .contacts { position: absolute; right: 37px; top: 276px; list-style: none; }
  .contacts li {
    display: flex; align-items: center; justify-content: flex-end; gap: 12px;
    color: var(--ink); font-weight: 300; font-size: 15px; line-height: 23px;
  }
  .contacts svg { width: 14px; height: 14px; fill: var(--brand-red); }
</style>
</head>
<body>

<section class="card card-reverse" aria-label="Card reverse">
  <div class="brand-name">Vexalund</div>
  <div class="tagline">Care Beyond Borders</div>
</section>

<section class="card card-front" aria-label="Card front">
  <svg class="wave" viewBox="0 0 620 376" aria-hidden="true">
    <path fill="var(--brand-blue)" d="M0,0 H620 V98 C580,112 530,124 470,118 C380,110 300,12 180,8 C110,6 50,25 0,45 Z"/>
    <path fill="var(--brand-red)" d="M0,66 C60,30 120,18 180,22 C290,30 360,118 460,128 C530,134 580,120 620,105 V128 C580,140 520,148 450,145 C350,140 280,40 160,34 C100,32 40,60 0,88 Z"/>
  </svg>

  <div class="person">
    <div class="person-name">Arjun K. Malvade</div>
    <div class="person-role">CEO, Vexalund</div>
  </div>

  <div class="brand-name">Vexalund</div>

  <address class="address">
    12, Sunrise Colony,<br>Nagpur-440010 (INDIA)
  </address>

  <ul class="contacts">
    <li>+91-9000012345
      <svg viewBox="0 0 16 16" aria-hidden="true"><path d="M1 5 C1 2 15 2 15 5 V7 H11 V5 H5 V7 H1 Z M3 8 H13 L14 14 H2 Z"/></svg>
    </li>
    <li>akmalvade@vexalund.com
      <svg viewBox="0 0 16 16" aria-hidden="true"><path d="M1 3 H15 V13 H1 Z M2 4 L8 9 L14 4 V5 L8 10 L2 5 Z" fill-rule="evenodd"/></svg>
    </li>
    <li>https://vexalund.com
      <svg viewBox="0 0 16 16" aria-hidden="true"><path d="M8 1 A7 7 0 1 0 8 15 A7 7 0 1 0 8 1 Z M8 2.5 C6.5 4 6 6 6 8 C6 10 6.5 12 8 13.5 C9.5 12 10 10 10 8 C10 6 9.5 4 8 2.5 Z M2.5 7.4 H13.5 V8.6 H2.5 Z" fill-rule="evenodd"/></svg>
    </li>
  </ul>
</section>

</body>
</html>
```